Creative, fresh business card design for Ripplecraft Facades

We need a fresh, creative business card design for Ripplecraft Facades. We are the manufacturer of Ripplecraft Facades in Australia. Wall panels are 2400 x 1200mm panels made from MDF and feature 3D patterns on the face of the panel. The colours to be used are green, silver/grey and white RGB
Red 187
Green 207
Blue 65.

An idea is to possibly use a watermark of one of our designs as a background (like on the "Grids" design on the left hand side of page 2 of our brochure).

Target Market(s)

Interior designers, architects, builders and home renovators

Industry/Entity Type

Business

Contact Information for Business Card

Details to go on the card are:
Our logo (attached),
Slogan: "Decorative panels for interiors and exteriors",
Contact name,
Position,
Mobile phone number,
Business address,
Business phone,
Business fax,
Website and
Email address.

I have attached a few images of our panels and our brochure for reference.

The colours of the business card should feature our logo colours which are: RGB
Red 187
Green 207
Blue 65

Requirements
Must have
• Very modern fonts and design. Some of the designs shown especially the "Prisms" design which is a popular design.
Nice to have
• Creative but simple design. Very contemporary.
Should not have
• Anything ornate or old fashioned.

```html
<!DOCTYPE html>
<html lang="en">
<head>
<meta charset="utf-8">
<title>Ripplecraft Facades – Business Card</title>
<link rel="stylesheet" href="https://fonts.googleapis.com/css2?family=Arimo:wght@400;700&display=swap">
<style>
  :root {
    --lime: #bfd631;
    --grey: #8a8a8c;
    --grey-dark: #555557;
    --rule: #a9a9ad;
    --white: #ffffff;
    --backdrop: #ecece8;
  }
  * { margin: 0; padding: 0; box-sizing: border-box; }
  html, body {
    width: 1200px; height: 987px; overflow: hidden;
    background: var(--backdrop);
    font-family: "Arimo", Arial, sans-serif;
  }
  .canvas { position: relative; width: 1200px; height: 987px; }

  .card {
    position: absolute; left: 292px; width: 616px; height: 352px;
    box-shadow: 0 2px 8px rgba(0,0,0,.18);
  }
  .card--front { top: 130px; background: var(--white); }
  .card--back  { top: 505px; background: var(--lime); }

  /* brand block */
  .brand { position: absolute; }
  .card--front .brand { left: 68px; top: 100px; width: 205px; }
  .card--back  .brand { left: 394px; top: 170px; width: 190px; }
  .brand__name {
    display: flex; align-items: flex-start; gap: 10px;
    font-weight: 700; font-size: 33px; line-height: 1.02;
  }
  .card--front .brand__name { color: var(--lime); }
  .card--back  .brand__name { color: var(--white); }
  .brand__mark { flex: none; width: 22px; height: 22px; margin-top: 6px; }
  .card--front .brand__mark { background: var(--grey); }
  .card--back  .brand__mark { background: var(--white); }
  .brand__slogan {
    margin-top: 12px; font-size: 11.5px; letter-spacing: 2.1px;
    line-height: 1.2; text-align: center;
  }
  .card--front .brand__slogan { color: var(--grey); }
  .card--back  .brand__slogan { color: var(--white); }
  .brand__web { margin-top: 6px; font-size: 15px; color: var(--white); text-align: center; }

  /* front details */
  .divider {
    position: absolute; left: 308px; top: 75px; width: 1px; height: 210px;
    background: #d7d7d9;
  }
  .details { position: absolute; left: 335px; top: 77px; color: var(--grey-dark); }
  .details__name { font-weight: 700; font-size: 22px; color: var(--lime); letter-spacing: .3px; }
  .details__role { font-size: 17px; color: var(--grey); margin-top: 2px; }
  .details__address { font-size: 17px; line-height: 23px; margin-top: 15px; }
  .contacts { list-style: none; margin-top: 8px; font-size: 17px; line-height: 23.4px; }
  .contacts li { display: flex; align-items: center; gap: 8px; }
  .contacts svg { width: 15px; height: 15px; fill: var(--lime); flex: none; }

  .front-rule { position: absolute; left: 0; right: 0; top: 327px; height: 2px; background: var(--rule); }
  .front-band { position: absolute; left: 0; right: 0; top: 331px; bottom: 0; background: var(--lime); }
</style>
</head>
<body>
<main class="canvas">

  <section class="card card--front" aria-label="Business card front">
    <div class="brand">
      <div class="brand__name"><span>Ripplecraft<br>Facades</span><span class="brand__mark"></span></div>
      <p class="brand__slogan">decorative panels for<br>interiors &amp; landscapes</p>
    </div>

    <div class="divider"></div>

    <div class="details">
      <p class="details__name">DANIEL HART</p>
      <p class="details__role">CEO&amp;Founder</p>
      <p class="details__address">4120 Wattle Crescent<br>Geelong, Victoria 3220</p>
      <ul class="contacts">
        <li>
          <svg viewBox="0 0 16 16" aria-hidden="true"><path d="M3.6 1.2l2.3 2.7-1.3 1.9c.9 2 2.6 3.8 4.6 4.7l1.9-1.3 2.7 2.3-1.3 2.4C7.4 14 2 8.6 1.2 3.4z"/></svg>
          (555) 214-7390
        </li>
        <li>
          <svg viewBox="0 0 16 16" aria-hidden="true"><rect x="4" y="1.5" width="8" height="4"/><rect x="1" y="6.5" width="14" height="6" rx="1"/><rect x="4" y="11" width="8" height="3.5"/></svg>
          (555) 214-7391
        </li>
        <li>
          <svg viewBox="0 0 16 16" aria-hidden="true"><path d="M1 3.5h14v9H1z M1.8 4.2L8 9l6.2-4.8" stroke="#fff" stroke-width="1"/></svg>
          dhart@ripplecraftfacades.com
        </li>
        <li>
          <svg viewBox="0 0 16 16" aria-hidden="true"><circle cx="8" cy="8" r="7"/><path d="M1 8h14M8 1c-2.5 2.2-2.5 11.8 0 14M8 1c2.5 2.2 2.5 11.8 0 14" stroke="#fff" stroke-width=".9" fill="none"/></svg>
          www.ripplecraftfacades.com
        </li>
      </ul>
    </div>

    <div class="front-rule"></div>
    <div class="front-band"></div>
  </section>

  <section class="card card--back" aria-label="Business card back">
    <div class="brand">
      <div class="brand__name"><span>Ripplecraft<br>Facades</span><span class="brand__mark"></span></div>
      <p class="brand__slogan">decorative panels for<br>interiors &amp; landscapes</p>
      <p class="brand__web">www.ripplecraftfacades.com</p>
    </div>
  </section>

</main>
</body>
</html>
```